Quill Harbor (IT/Network Services)

Quill Harbor, LLC provides technology services to small and medium businesses. Essentially, anytime you've every thought your business might need an "IT guy" to handle something you could instead call us to handle it. Basically, you can outsource your IT needs to us.

This is a brand new company and so we'll need a brand new website. I'd like to use WordPress to handle the site since that will make things easier for me to maintain in the long run.

The site should include a, more-or-less, static front page with the dynamic data occurring on pages linked from a navigational area.

I have a logo already designed that I would like to see used in the design. The one with "white" in the title is the official logo, just added some other versions for your perusal.

Color queues from the logo but feel free to add other colors where applicable.

The site should feel somewhat corporate but with a "younger" slant (something a 25-35 year old would enjoy).

Pages (either to be added initially or by me after design completion):
"About" section - includes company history, business philosophy, etc.
"Services" section - service options, service approach, service specifics
"Testimonials" section - (eventually)
"News" section - (eventually) industry news, company news, events, blog
Contact Links

Websites to view:
The two largest local competitors:
http://www.brightmarsh-tech.example/
http://www.kelvarworks.example/
Other local competitors:
http://www.tpbllc.example/
http://www.morrowfield.example/

Other info you might find useful:
Domain: qhllc.example
Address:
417 Elm Row S
Suite 512B
Nashville, TN 37288
Phone: 615-555-0187
Emails available for use/display:
info@qhllc.example
sales@qhllc.example

Target Market(s)

Our target clients are mainly small businesses (25 or less computer users) which means we're looking at a lot of start-ups or younger companies. We'll be interacting with many entrepreneurs and young business owners.

Requirements
Must have
• Need full WP theme (not a mockup)

```html
<!DOCTYPE html>
<html lang="en">
<head>
<meta charset="utf-8">
<title>Quill Harbor — IT &amp; Network Services</title>
<link rel="stylesheet" href="https://fonts.googleapis.com/css2?family=Noto+Sans:wght@300;400;500;700&family=Nunito:wght@600;700;800&display=swap">
<style>
:root{
  --bg:#e9e8ee;
  --green:#6cb52a;
  --green-dark:#4f8f17;
  --green-soft:#c9e6ae;
  --nav:#2d2d2d;
  --text:#333;
  --muted:#666;
  --line:#cfcfd6;
  --link:#1a5fb4;
  --red:#d40000;
  --logo:#6f7377;
}
*{box-sizing:border-box;margin:0;padding:0}
html,body{width:1200px;height:1136px;overflow:hidden}
body{background:var(--bg);font-family:"Noto Sans",sans-serif;color:var(--text);font-size:11px;position:relative}
.abs{position:absolute}

.header{left:0;top:0;width:1200px;height:104px;background:linear-gradient(#f3f3f7,#e6e6ec)}
.header .cloud{left:380px;top:0;width:620px;height:104px;background:radial-gradient(ellipse at 50% 85%,#fff 0,#fafafc 40%,rgba(255,255,255,0) 70%)}
.brand{left:110px;top:24px;display:flex;align-items:center;gap:10px;font-family:"Nunito",sans-serif;font-weight:800;font-size:40px;line-height:48px;color:var(--logo);letter-spacing:1px}
.brand .dot{width:18px;height:18px;border-radius:50%;background:#9aa0a4}
.search{left:505px;top:25px;width:265px;height:28px;border:2px solid var(--green);border-radius:14px;background:#fff;display:flex;align-items:center;justify-content:space-between;overflow:hidden}
.search span{font-family:"Nunito",sans-serif;font-size:19px;color:#333;padding-left:11px}
.search .btn{width:56px;height:100%;background:var(--green);border-radius:14px 0 0 14px;display:flex;align-items:center;justify-content:center}
.rss{left:887px;top:24px;width:81px;height:27px;background:var(--green);border-radius:4px;display:flex;align-items:center;justify-content:center;gap:4px;color:#fff;font-family:"Nunito",sans-serif;font-weight:800;font-size:19px}

.nav{left:0;top:104px;width:1200px;height:34px;background:var(--nav)}
.nav a{position:absolute;top:0;height:34px;line-height:34px;color:#fff;text-decoration:none;font-size:17px}
.nav .home{left:150px;width:39px;top:-3px;height:37px;line-height:40px;background:var(--green);text-align:center;font-size:13px}
.nav .about{left:215px;font-family:"Nunito",sans-serif;font-weight:700;letter-spacing:1px}
.band{left:0;top:138px;width:1200px;height:27px;background:var(--green)}

.featured{left:150px;top:179px;width:900px;display:grid;grid-template-columns:repeat(3,300px);row-gap:8px}
.feat{display:flex;gap:12px;height:96px}
.thumb{border:1px solid #ccc;background:#fff;padding:2px;flex:none}
.thumb div{width:100%;height:100%}
.feat .thumb{width:96px;height:96px}
.feat h4{font-weight:400;font-size:11px;color:#222;margin:6px 0 12px 6px;white-space:nowrap;overflow:hidden;text-overflow:ellipsis;width:180px}
.feat p{font-size:10.5px;line-height:17px;color:#555;width:182px;height:51px;overflow:hidden}
.divider{height:1px;background:var(--line)}

.crumb{left:150px;top:401px;font-size:11.5px}
.crumb a{color:var(--link);text-decoration:none}
.tools{left:769px;top:397px;display:flex;gap:12px;align-items:center;font-size:10.5px}
.tools i{display:inline-block;width:13px;height:13px;margin-right:6px;vertical-align:-2px}

.post{left:158px;width:584px}
.post .thumb{position:absolute;left:0;top:0;width:132px;height:96px;border:2px solid #7fc24a;padding:0}
.meta{position:absolute;left:0;top:106px;width:132px;text-align:center;font-size:11px;line-height:15.5px;color:#111}
.post h2{position:absolute;left:154px;top:0;width:432px;font-weight:400;font-size:18px;line-height:22px;color:#222;white-space:nowrap;overflow:hidden;text-overflow:ellipsis}
.post h2 .ic{display:inline-block;width:16px;height:16px;border-radius:50%;background:var(--green);margin-right:5px;vertical-align:-2px}
.post p{position:absolute;left:154px;top:30px;width:432px;font-size:12.5px;line-height:20.3px;color:#666;font-weight:300}
.tags{position:absolute;left:0;font-size:12px;color:#555;display:flex;align-items:center;gap:6px}
.tags .sq{width:12px;height:12px;background:linear-gradient(135deg,#e84 50%,#5b3 50%)}
.tags b{font-weight:400;color:var(--red)}
.more{position:absolute;left:480px;width:72px;height:22px;border-radius:11px;background:linear-gradient(#a9dc6a,#6cb52a);color:#111;font-size:11.5px;text-align:center;line-height:22px}
.post .sep{position:absolute;left:0;width:584px;height:2px;background:var(--line)}

.promo{left:769px;top:441px;width:277px;height:230px;background:linear-gradient(135deg,#262a24,#3f6a1c 60%,#6cb52a);color:#fff;overflow:hidden}
.promo .photo{position:absolute;right:0;top:0;width:110px;height:230px;background:linear-gradient(#c9d3da,#a7b4bd 60%,#6b7b86)}
.promo .tagline{position:absolute;left:14px;top:6px;background:#fff;color:var(--green-dark);font-weight:700;font-size:13px;padding:3px 8px;border-radius:0 0 10px 10px}
.promo .s1{position:absolute;left:14px;top:46px;font-size:14px}
.promo .s2{position:absolute;left:13px;top:70px;font-family:"Nunito",sans-serif;font-weight:800;font-size:30px;line-height:34px;color:#e6f3d6}
.promo .s3{position:absolute;left:14px;top:150px;font-size:13px;line-height:19px}
.promo .s3 em{font-style:normal;color:#f7d400;font-weight:700;font-size:16px}

.widget-h{left:765px;width:285px;height:30px;background:var(--green);color:#fff;font-size:15px;display:flex;align-items:center;gap:6px;padding-left:8px;border-bottom:2px solid var(--green-soft)}
.widget-h .n{width:18px;height:18px;border:1.5px solid #fff;border-radius:50%;font-size:11px;text-align:center;line-height:15px;font-family:"Nunito",sans-serif}
.avatars{left:767px;top:719px;display:grid;grid-template-columns:repeat(7,37px);gap:4px 3.5px}
.avatars div{width:37px;height:37px;background:#bfc3c8}
.comments{left:771px;top:890px;width:275px}
.comment{display:flex;gap:10px;height:61px;border-bottom:1px dashed #d0d0d6;padding-top:4px;margin-bottom:3px}
.comment .av{width:38px;height:38px;background:#9aa4ad;flex:none;margin-top:6px;border:1px solid #ddd}
.comment small{display:block;font-size:10.5px;color:#555}
.comment span{display:block;font-size:12px;color:#111;line-height:18px;margin-top:2px}
</style>
</head>
<body>
<header class="header abs">
  <div class="cloud abs"></div>
  <div class="brand abs"><span>QUILL HARBOR</span><span class="dot"></span></div>
  <div class="search abs"><span>search</span><div class="btn">
    <svg width="26" height="22" viewBox="0 0 26 22"><circle cx="10" cy="10" r="8" fill="#222"/><line x1="16" y1="15" x2="23" y2="20" stroke="#222" stroke-width="3"/></svg></div></div>
  <div class="rss abs"><svg width="16" height="16" viewBox="0 0 16 16"><circle cx="3" cy="13" r="2.3" fill="#fff"/><path d="M2 7a7 7 0 0 1 7 7M2 2a12 12 0 0 1 12 12" fill="none" stroke="#fff" stroke-width="2.3"/></svg>RSS</div>
</header>
<nav class="nav abs"><a class="home" href="#">Home</a><a class="about" href="#">about us</a></nav>
<div class="band abs"></div>

<section class="featured abs">
  <div class="feat"><div class="thumb"><div role="img" aria-label="Office network rack" style="background:linear-gradient(#f4f4f4,#cfd9e6)"></div></div><div><h4>Managed networks for small offices</h4><p>We design, install and watch over your office network so your team never waits on a slow connection again...</p></div></div>
  <div class="feat"><div class="thumb"><div role="img" aria-label="Technician at a desk" style="background:linear-gradient(#b9c3cc,#7f9a6a 55%,#5a5e58)"></div></div><div><h4>Your on-call IT guy, without the hire</h4><p>Outsource the day-to-day IT work to Quill Harbor and get a dedicated team for the price of a part-time...</p></div></div>
  <div class="feat"><div class="thumb"><div role="img" aria-label="Cloud backup dashboard" style="background:linear-gradient(#e7f3dc,#cfe6b9)"></div></div><div><h4>Cloud backup that just works</h4><p>Nightly encrypted backups of every laptop and server, tested monthly so restores are never a gamble...</p></div></div>
  <div class="feat"><div class="thumb"><div role="img" aria-label="Security monitoring screen" style="background:linear-gradient(#2d3a2a,#0e120e)"></div></div><div><h4>Security checkups for start-ups</h4><p>A one-day audit of passwords, firewalls and devices, with a plain-English report of what to fix first...</p></div></div>
  <div class="feat"><div class="thumb"><div role="img" aria-label="Email setup on a laptop" style="background:linear-gradient(#e9f2fb,#bcd6ef)"></div></div><div><h4>Email and accounts, set up right</h4><p>Company email, shared calendars and user accounts configured on day one and kept tidy as you grow...</p></div></div>
  <div class="feat"><div class="thumb"><div role="img" aria-label="New workstation setup" style="background:linear-gradient(#eef5e6,#d7e8c7)"></div></div><div><h4>New hire? New machine, ready</h4><p>We order, image and deliver workstations so new team members are productive from their first hour...</p></div></div>
</section>
<div class="divider abs" style="left:150px;top:386px;width:900px"></div>

<div class="crumb abs">You are here: <a href="#">Home</a></div>
<div class="tools abs">
  <span><i style="background:#f4b400;clip-path:polygon(50% 0,62% 35%,100% 38%,70% 60%,80% 100%,50% 77%,20% 100%,30% 60%,0 38%,38% 35%)"></i>Bookmark</span>
  <span><i style="background:#2a5bd7;border-radius:2px"></i>Share</span>
  <span><i style="border:1px solid #999;background:#fff"></i>Copy link</span>
  <span><i style="background:var(--green)"></i>More</span>
</div>

<article class="post abs" style="top:438px;height:226px">
  <div class="thumb"><div role="img" aria-label="Server room" style="background:linear-gradient(135deg,#3c4a56,#c8d0d6 50%,#4f8f17)"></div></div>
  <div class="meta">Posted by Quill Harbor<br>Views: 28<br>Category: Services<br>Comments: 1<br>Date: 2012-05-24</div>
  <h2><span class="ic"></span>Why small businesses outsource their IT to a partner</h2>
  <p>Most companies with fewer than 25 computers do not need a full-time IT department, but they do need someone who answers the phone when the printer, the Wi-Fi or the email stops working. Quill Harbor fills that role: we learn your setup, keep it patched and backed up, and fix problems before they cost you a workday. One flat monthly plan covers support, monitoring and advice, so you can get back to running...</p>
  <div class="tags" style="top:201px"><span class="sq"></span><b>Tags:</b>IT support, outsourcing, small business</div>
  <div class="more" style="top:197px">Read more</div>
  <div class="sep" style="top:224px"></div>
</article>

<article class="post abs" style="top:681px;height:200px">
  <div class="thumb"><div role="img" aria-label="Office Wi-Fi setup" style="background:linear-gradient(135deg,#e6efdc,#f3f3f3 50%,#d9dde3)"></div></div>
  <div class="meta">Posted by Quill Harbor<br>Views: 63<br>Category: Networks<br>Comments: 6<br>Date: 2012-05-22</div>
  <h2><span class="ic"></span>Five signs your office network needs attention</h2>
  <p>Dropped video calls, shared drives that take forever to open and a router nobody remembers the password for are all warning signs. In this post we walk through five quick checks any owner can do in an afternoon, what each result means, and when it makes sense to bring in help. We also explain how our network assessment works, what it costs and the simple report you receive at the end...</p>
</article>

<article class="post abs" style="top:896px;height:230px">
  <div class="thumb"><div role="img" aria-label="Backup drives on a shelf" style="background:linear-gradient(135deg,#1c2a55,#5a7bc2 50%,#e8eef8)"></div></div>
  <div class="meta">Posted by Quill Harbor<br>Views: 110<br>Category: Backup<br>Comments: 3<br>Date: 2012-05-15</div>
  <h2><span class="ic"></span>Backups you can trust: our approach to data safety</h2>
  <p>A backup only counts if you can restore from it. That is why every Quill Harbor plan includes automatic nightly copies to two locations, alerts when a job fails and a monthly test restore of real files. Here is how the process works, what we protect by default, and how long it takes to get a laptop or a whole server back after a crash...</p>
  <div class="tags" style="top:201px"><span class="sq"></span><b>Tags:</b>backup, cloud, data safety, recovery</div>
  <div class="more" style="top:197px">Read more</div>
  <div class="sep" style="top:224px"></div>
</article>

<aside>
  <div class="promo abs">
    <div class="photo" role="img" aria-label="Technician helping a client"></div>
    <div class="tagline">IT made easy</div>
    <div class="s1">Outsource your IT</div>
    <div class="s2">Quill<br>Harbor</div>
    <div class="s3">Call <em>615-555-0187</em><br>info@qhllc.example</div>
  </div>
  <div class="widget-h abs" style="top:680px"><span class="n">N</span>Businesses we support</div>
  <div class="avatars abs" role="img" aria-label="Client avatars">
    <div style="background:#b98a6a"></div><div style="background:#8a8f86"></div><div style="background:#56614f"></div><div style="background:#e33"></div><div style="background:#c9a25a"></div><div style="background:#d6d8db"></div><div style="background:#6d5a4c"></div>
    <div style="background:#d6d8db"></div><div style="background:#7cc04a"></div><div style="background:#a37bd6"></div><div style="background:#8a3355"></div><div style="background:#7e806c"></div><div style="background:#d6d8db"></div><div style="background:#233b2c"></div>
    <div style="background:#3a8fd6"></div><div style="background:#9a7a5c"></div><div style="background:#d6d8db"></div><div style="background:#7cc04a"></div><div style="background:#c9b9a8"></div><div style="background:#d6d8db"></div><div style="background:#a9a08a"></div>
  </div>
  <div class="widget-h abs" style="top:853px"><span class="n">N</span>What clients say</div>
  <div class="comments abs">
    <div class="comment"><div class="av" role="img" aria-label="Client avatar" style="background:#4b5866"></div><div><small>Dana, studio owner said:</small><span>They fixed our Wi-Fi the same day</span></div></div>
    <div class="comment"><div class="av" role="img" aria-label="Client avatar" style="background:#1d2f48"></div><div><small>Marcus, start-up founder said:</small><span>Like having an IT team without the payroll cost</span></div></div>
    <div class="comment"><div class="av" role="img" aria-label="Client avatar" style="background:#d6d8db"></div><div><small>Priya, clinic manager said:</small><span>Fast, friendly and always clear!</span></div></div>
    <div class="comment"><div class="av" role="img" aria-label="Client avatar" style="background:#c8d2c4"></div><div><small>Leo, agency partner said:</small><span>Our backups finally just work</span></div></div>
  </div>
</aside>
</body>
</html>
```